Design a compelling Tarnwove Business Card that will drive people to my site

I want a business card that I can give to people—less to tell them who I am and more to direct them to my website. My website is a portal for Pelmor Aquatics Officials and a place for people who want to become Pelmor Aquatics Officials.
I am uploading my official company logo as well as a business card mockup that I did on my own. Please feel free to completely stray from this design.
I've included a screen recording of the homepage of my website as well.
Target Market(s)
Pelmor Aquatics Officials and people who desire to become one
Contact Information for Business Card
website url
Look and feel
Each slider illustrates characteristics of the customer's brand and the style your logo design should communicate.

```html
<!DOCTYPE html>
<html lang="en">
<head>
<meta charset="utf-8">
<title>Tarnwove Business Card</title>
<link rel="stylesheet" href="https://fonts.googleapis.com/css2?family=Poppins:wght@400;600;700&display=swap">
<style>
  :root {
    --brand-blue: #3a52a5;
    --brand-deep: #2b3f8c;
    --brand-light: #93a9dc;
    --brand-mid: #6a84d4;
    --paper: #ffffff;
    --ink-grey: #4a4a4a;
    --backdrop: #e9ebf1;
  }
  html, body {
    margin: 0;
    width: 1200px;
    height: 900px;
    overflow: hidden;
    background: var(--backdrop);
    font-family: "Poppins", sans-serif;
  }
  .sheet {
    width: 1200px;
    height: 900px;
    display: flex;
    flex-direction: column;
    align-items: center;
    justify-content: center;
    gap: 40px;
  }
  .card {
    position: relative;
    width: 700px;
    height: 400px;
    border-radius: 4px;
    overflow: hidden;
    box-shadow: 0 6px 20px rgba(30, 40, 80, 0.18);
  }
  .card-front { background: var(--paper); }
  .card-back { background: var(--brand-blue); }
  .card-waves {
    position: absolute;
    inset: 0;
    width: 100%;
    height: 100%;
  }
  .wordmark {
    position: absolute;
    margin: 0;
    font-weight: 700;
    letter-spacing: -1px;
    line-height: 1;
  }
  .card-front .wordmark {
    top: 40px;
    left: 70px;
    font-size: 64px;
    color: var(--brand-blue);
  }
  .card-back .wordmark {
    top: 60px;
    right: 60px;
    font-size: 96px;
    color: var(--paper);
  }
  .holder {
    position: absolute;
    top: 150px;
    right: 50px;
    text-align: right;
  }
  .holder-name {
    margin: 0;
    font-size: 26px;
    font-weight: 700;
    color: var(--brand-blue);
  }
  .holder-name .surname { color: var(--brand-light); }
  .holder-title {
    margin: 2px 0 0;
    font-size: 18px;
    font-weight: 400;
    color: var(--ink-grey);
  }
  .contact {
    position: absolute;
    right: 200px;
    bottom: 14px;
    margin: 0;
    padding: 0;
    list-style: none;
    text-align: right;
    color: var(--paper);
    font-size: 16px;
    line-height: 1.45;
  }
  .contact li {
    display: flex;
    align-items: center;
    justify-content: flex-end;
    gap: 8px;
  }
  .contact svg { width: 14px; height: 14px; flex: none; }
  .tagline {
    position: absolute;
    right: 40px;
    bottom: 22px;
    margin: 0;
    font-size: 20px;
    font-weight: 400;
    color: var(--brand-blue);
  }
</style>
</head>
<body>
<main class="sheet">

  <section class="card card-front" aria-label="Card front">
    <svg class="card-waves" viewBox="0 0 700 400" preserveAspectRatio="none" aria-hidden="true">
      <path fill="var(--brand-blue)" d="M0,0 L55,0 C10,130 70,230 270,268 C430,296 590,300 700,380 L700,400 L0,400 Z"/>
      <path fill="var(--brand-light)" d="M0,40 L30,40 C5,150 70,240 270,280 C430,308 560,318 650,400 L600,400 C520,330 420,318 260,295 C60,262 -10,170 0,40 Z"/>
      <path fill="var(--paper)" d="M70,0 L700,0 L700,370 C600,300 440,292 280,262 C90,226 30,130 70,0 Z"/>
    </svg>
    <h1 class="wordmark">Tarnwove</h1>
    <div class="holder">
      <p class="holder-name">Marcus <span class="surname">Delvane</span></p>
      <p class="holder-title">CEO &amp; Founder</p>
    </div>
    <ul class="contact">
      <li>(555) 201-4737
        <svg viewBox="0 0 16 16"><path fill="currentColor" d="M4 1l3 3-2 2c1 2 3 4 5 5l2-2 3 3-2 3C7 15 1 9 1 3z"/></svg>
      </li>
      <li>marcus@tarnwove.com
        <svg viewBox="0 0 16 16"><rect x="1" y="3" width="14" height="10" rx="1" fill="currentColor"/><path d="M1 4l7 5 7-5" stroke="var(--brand-blue)" stroke-width="1.4" fill="none"/></svg>
      </li>
      <li>www.tarnwove.com
        <svg viewBox="0 0 16 16"><circle cx="8" cy="8" r="7" fill="currentColor"/><path d="M1 8h14M8 1c3 3 3 11 0 14M8 1c-3 3-3 11 0 14" stroke="var(--brand-blue)" stroke-width="1" fill="none"/></svg>
      </li>
    </ul>
  </section>

  <section class="card card-back" aria-label="Card back">
    <svg class="card-waves" viewBox="0 0 700 400" preserveAspectRatio="none" aria-hidden="true">
      <path fill="var(--brand-deep)" d="M0,60 C40,200 200,250 420,268 C540,278 640,300 700,330 L700,345 C600,312 480,300 360,292 C150,278 10,210 0,60 Z"/>
      <path fill="var(--brand-mid)" d="M0,210 C120,300 360,300 560,312 C630,318 680,330 700,340 L700,352 C620,334 480,326 320,318 C160,310 60,280 0,240 Z"/>
      <path fill="var(--brand-light)" d="M0,235 C100,300 320,312 520,322 C610,328 670,340 700,352 L700,400 L0,400 Z"/>
    </svg>
    <h2 class="wordmark">Tarnwove</h2>
    <p class="tagline">The Poolside Referee’s Gateway</p>
  </section>

</main>
</body>
</html>
```